Meadowlark Property Review is a leading provider of residential appraisal and home inspection products in S

I need a business card/logo designed that obviously describes my business. We are a residential appraisal and home inspection company in Springfield, MO. We offer residential appraisals, home inspection, pest inspection and radon gas measurement. We have been in business for 18 years and hold state certified residential appraisal licenses and OBREX certified home inspection licenses. I have a logo that I really like and will attach, but would be open to new suggestions. I like more modern designs than traditional and would like a two sided card with our services, licenses and qualifications on the back.

```html
<!DOCTYPE html>
<html lang="en">
<head>
<meta charset="utf-8">
<title>Meadowlark Property Review — Business Card</title>
<link href="https://fonts.googleapis.com/css2?family=Open+Sans:wght@400;600;700&display=swap" rel="stylesheet">
<style>
  :root{
    --bg:#ece8e2;
    --card:#ffffff;
    --orange:#f39a22;
    --tan:#e9dccb;
    --tan-deep:#cdb597;
    --brown:#8a6a43;
    --ink:#2e2a26;
    --gold:#d9ae3c;
  }
  *{margin:0;padding:0;box-sizing:border-box}
  html,body{width:1200px;height:913px;overflow:hidden}
  body{background:var(--bg);font-family:"Open Sans",Arial,sans-serif;color:var(--ink);position:relative}

  .card{position:absolute;width:525px;height:300px;background:var(--card);border-radius:16px;
        box-shadow:0 6px 18px rgba(0,0,0,.14);overflow:hidden}
  .card--front{left:45px;top:306px}
  .card--back{left:630px;top:306px}

  .swoosh{position:absolute;inset:0;width:100%;height:100%}

  /* wordmark */
  .wordmark{position:absolute;display:flex;align-items:center;gap:10px}
  .wordmark__dot{width:12px;height:12px;border-radius:50%;background:var(--orange);flex:none}
  .wordmark__name{font-weight:700;color:var(--brown);line-height:1.1}
  .card--front .wordmark{left:88px;top:112px}
  .card--front .wordmark__name{font-size:21px;width:170px}
  .card--back .wordmark{left:0;right:0;top:48px;justify-content:center}
  .card--back .wordmark__name{font-size:24px}

  .cert-badge{position:absolute;left:40px;top:134px;width:36px;height:36px;border-radius:50%;
              background:var(--gold);border:3px solid #f4d98a}

  /* contact block */
  .contact{position:absolute;left:300px;top:30px;width:210px}
  .contact__name{font-size:20px;font-weight:700;letter-spacing:.5px;line-height:1}
  .contact__role{font-size:11px;color:var(--orange);font-weight:600;letter-spacing:.5px;margin-top:4px}
  .contact__list{list-style:none;margin-top:10px;border-left:1px solid var(--tan-deep);padding-left:10px}
  .contact__list li{display:flex;align-items:center;gap:8px;font-size:12.5px;line-height:19px;white-space:nowrap}
  .contact__list svg{width:11px;height:11px;flex:none;fill:none;stroke:var(--orange);stroke-width:2}

  .address{position:absolute;left:120px;bottom:30px;font-size:9.5px;color:var(--ink);white-space:nowrap;
           transform:rotate(-11deg);transform-origin:left bottom}

  /* back */
  .services{position:absolute;left:0;right:0;top:118px;list-style:none;text-align:center}
  .services li{font-size:14px;letter-spacing:.4px;line-height:19px;text-transform:uppercase}
  .services li:nth-child(5){font-weight:600}
  .tagline{position:absolute;left:24px;right:24px;bottom:22px;font-size:9.5px;font-weight:700;line-height:13px}
</style>
</head>
<body>

<section class="card card--front" aria-label="Card front">
  <svg class="swoosh" viewBox="0 0 525 300" preserveAspectRatio="none" aria-hidden="true">
    <defs>
      <linearGradient id="band" x1="0" y1="0" x2="1" y2="1">
        <stop offset="0" stop-color="#f3ebe0"/>
        <stop offset="1" stop-color="#dcc7aa"/>
      </linearGradient>
    </defs>
    <path d="M0,300 C150,255 320,180 525,150 L525,300 Z" fill="url(#band)"/>
    <path d="M0,300 C150,255 320,180 525,150" fill="none" stroke="var(--orange)" stroke-width="4"/>
  </svg>

  <div class="cert-badge" aria-label="Certification badge"></div>
  <div class="wordmark">
    <span class="wordmark__dot"></span>
    <span class="wordmark__name">Meadowlark Property Review</span>
  </div>

  <div class="contact">
    <p class="contact__name">DANA WHITFIELD</p>
    <p class="contact__role">OWNER</p>
    <ul class="contact__list">
      <li><svg viewBox="0 0 12 12"><path d="M2 1h2.5l1 3-1.5 1a6 6 0 0 0 3 3l1-1.5 3 1V10a1.5 1.5 0 0 1-1.5 1.5A9.5 9.5 0 0 1 .5 2.5 1.5 1.5 0 0 1 2 1z"/></svg>417-555-0142</li>
      <li><svg viewBox="0 0 12 12"><rect x="3" y="1" width="6" height="10" rx="1"/><path d="M5.5 9h1"/></svg>417-555-0187</li>
      <li><svg viewBox="0 0 12 12"><rect x="1" y="2.5" width="10" height="7" rx="1"/><path d="M1 3l5 4 5-4"/></svg>info@meadowlarkreview.com</li>
      <li><svg viewBox="0 0 12 12"><circle cx="6" cy="6" r="5"/><path d="M1 6h10M6 1c-2.5 3-2.5 7 0 10M6 1c2.5 3 2.5 7 0 10"/></svg>www.meadowlarkreview.com</li>
    </ul>
  </div>

  <p class="address">Meadowlark Property Review 4410 S Fremont Avenue Suite C Springfield, MO 65804</p>
</section>

<section class="card card--back" aria-label="Card back">
  <div class="wordmark">
    <span class="wordmark__dot"></span>
    <span class="wordmark__name">Meadowlark Property Review</span>
  </div>
  <ul class="services">
    <li>Appraisal</li>
    <li>Home Inspection</li>
    <li>Termite</li>
    <li>Radon</li>
    <li>Well &amp; Septic Inspection</li>
    <li>Energy Audits</li>
  </ul>
  <p class="tagline">With years of experience behind us, we're prepared to tackle anything from a first Time buyer's starter home or a seasoned buyer purchasing a luxurious dream home</p>
</section>

</body>
</html>
```